Retail Jewelry Business Card Design Project

We are in need of a new business card design for a retail jewelry store. This store is in the business of fine jewelry including but not specific to bridal jewelry, diamonds, designer jewelry and watches.

This store has been in business for 20 years but continues to strive for a modern professional appeal. The main colors use for this business are a royal blue, white and silver.

Target Market(s)

Target market is ages 18-50

Industry/Entity Type

Jewelry

Requirements
Must have
• Sales Person Name
Sales Person Email Address

Store Address
Store Phone
Website

Standard business card size. No odd shapes or sizes.
Nice to have
• Overall modern feel for card.

We have thought that a design with a nice feature of the logo on the back of the card would be nice but open to ideas.
Should not have
• No specific images of jewelry should be used.

```html
<!DOCTYPE html>
<html lang="en">
<head>
<meta charset="utf-8">
<title>Halloway Fine Jewelry – Business Card</title>
<link rel="stylesheet" href="https://fonts.googleapis.com/css2?family=Jost:wght@400;500&display=swap">
<style>
  :root {
    --royal-blue: #2e3192;
    --ink: #231f20;
    --silver: #808285;
    --card: #ffffff;
    --backdrop: #e9e9ec;
  }
  * { margin: 0; padding: 0; box-sizing: border-box; }
  html, body { width: 1200px; height: 751px; overflow: hidden; }
  body {
    background: var(--backdrop);
    font-family: "Jost", sans-serif;
    color: var(--ink);
    position: relative;
  }
  .card {
    position: absolute;
    top: 230px;
    width: 525px;
    height: 300px;
    background: var(--card);
    border-radius: 26px;
    box-shadow: 0 2px 10px rgba(0,0,0,0.12);
    overflow: hidden;
  }
  .card--front { left: 50px; }
  .card--back { left: 625px; }

  .accent-bar {
    position: absolute;
    left: 0; top: 58px;
    width: 10px; height: 36px;
    background: var(--royal-blue);
  }
  .person-name {
    position: absolute;
    left: 44px; top: 58px;
    font-size: 19px;
    font-weight: 500;
    color: var(--royal-blue);
  }
  .brand-mark {
    position: absolute;
    right: 36px; top: 74px;
    font-size: 24px;
    font-weight: 500;
    color: var(--royal-blue);
    letter-spacing: 0.5px;
  }
  .address {
    position: absolute;
    left: 44px; top: 128px;
    font-size: 14px;
    line-height: 1.4;
    font-weight: 400;
  }
  .contact {
    position: absolute;
    left: 44px; top: 200px;
    font-size: 14px;
    line-height: 1.6;
    list-style: none;
  }
  .contact li { display: flex; align-items: center; gap: 7px; }
  .contact svg { width: 11px; height: 11px; fill: var(--royal-blue); }
  .website {
    position: absolute;
    left: 44px; top: 256px;
    font-size: 15px;
    letter-spacing: 1px;
    color: var(--ink);
  }
  .website .domain { color: var(--royal-blue); }

  .brand-mark--large {
    position: absolute;
    left: 0; right: 0; top: 100px;
    text-align: center;
    font-size: 42px;
    font-weight: 500;
    color: var(--ink);
    letter-spacing: 1px;
  }
  .website--back {
    position: absolute;
    left: 0; right: 0; top: 200px;
    text-align: center;
    font-size: 15px;
    letter-spacing: 3px;
    color: var(--ink);
  }
</style>
</head>
<body>
  <section class="card card--front" aria-label="Business card front">
    <span class="accent-bar"></span>
    <h1 class="person-name">Marcus Hale Whitfield</h1>
    <p class="brand-mark">Halloway Fine Jewelry</p>
    <address class="address">2280 Bayview Road<br>Harbor City, FL 32499</address>
    <ul class="contact">
      <li>
        <svg viewBox="0 0 12 12" aria-hidden="true"><path d="M2.5 0.8l2 2.2-1.1 1.4c.7 1.5 1.8 2.6 3.3 3.3l1.4-1.1 2.2 2-1.3 2.4C5 10.7 1.3 7 .6 2.1z"/></svg>
        555-014-2367
      </li>
      <li>
        <svg viewBox="0 0 12 12" aria-hidden="true"><path d="M0 3h12v7H0z M0 3l6 4 6-4" /></svg>
        marcus@hallowayjewelry.com
      </li>
    </ul>
    <p class="website">www.<span class="domain">hallowayjewelry</span>.com</p>
  </section>

  <section class="card card--back" aria-label="Business card back">
    <p class="brand-mark--large">Halloway Fine Jewelry</p>
    <p class="website--back">www.hallowayjewelry.com</p>
  </section>
</body>
</html>
```